Dental Practice Billboard Design

We are a newer dental practice in need of a simple but appealing billboard for our growing dental practice to attract new patients. The practice is owned by husband and wife dentists and is family friendly in a small town in Kentucky. We try to be very friendly and caring to our patients. Would prefer a blue background for the billboard and our tooth logo to be prominent. We are partial to the Patua One font used in the image below but please feel free to tweak it as you deem necessary. The shape of the uppercase D and lowercase g are why we like that font, so fonts with a similarly shaped “D” and “g” would work as well. Please include our phone number (555) 847-1390. Please see our website Harlowbrookdentistry.example for more info on the practice if needed. Thank you! Looking forward to seeing your creation.
Updates

The dimensions will be 12ft x 24ft (3.6576m x 7.3152m). Apologies for not including this in the original prompt. Thank you all for your submissions.

Industry/Entity Type

Dental

Font styles to use
Other font styles liked:
• Patua One

Colors
0054AA
0677BA
7BADD7
CADEEF
E8F1F8
0094D4
00A9DD
6FCCEA
C7EBF8
E9F6FB
00AB8E
00BBA5
67D7C9
C6EFE9
E9F9F6
59FF00
82FF00
B8FF75
E3FFCB
F4FFEA

Requirements
Must have
• Phone number, website, Logo, Practice name “Harlow Brook Dentistry”
Should not have
• A tagline or slogan

```html
<!DOCTYPE html>
<html lang="en">
<head>
<meta charset="UTF-8">
<title>Harlow Brook Dentistry Billboard</title>
<link href="https://fonts.googleapis.com/css2?family=Patua+One&display=swap" rel="stylesheet">
<style>
  :root {
    --navy: #1b2b58;
    --green: #2ab24c;
    --white: #ffffff;
  }
  * { margin: 0; padding: 0; box-sizing: border-box; }
  html, body {
    width: 1200px;
    height: 625px;
    overflow: hidden;
    background: var(--navy);
  }
  .billboard {
    position: relative;
    width: 1200px;
    height: 625px;
    background: var(--navy);
    font-family: "Patua One", Georgia, serif;
    color: var(--white);
  }
  .brand {
    position: absolute;
    top: 62px;
    left: 0;
    width: 1200px;
    height: 200px;
    display: flex;
    align-items: center;
    justify-content: center;
    gap: 30px;
  }
  .brand-mark {
    width: 150px;
    height: 150px;
    border-radius: 50%;
    background: var(--green);
    flex: none;
  }
  .brand-name {
    display: flex;
    flex-direction: column;
    font-weight: 400;
    line-height: 1;
    color: var(--white);
  }
  .brand-name .primary {
    font-size: 86px;
  }
  .brand-name .secondary {
    font-size: 44px;
    margin-top: 8px;
  }
  .web-band {
    position: absolute;
    top: 323px;
    left: 0;
    width: 1200px;
    height: 179px;
    background: var(--green);
  }
  .website {
    position: absolute;
    top: 360px;
    left: 0;
    width: 1200px;
    text-align: center;
    font-size: 40px;
    line-height: 52px;
    color: var(--white);
  }
  .phone-pill {
    position: absolute;
    top: 445px;
    left: 333px;
    width: 533px;
    height: 114px;
    border-radius: 57px;
    background: var(--green);
    border: 8px solid var(--navy);
    display: flex;
    align-items: center;
    justify-content: center;
    gap: 14px;
  }
  .phone-icon { width: 40px; height: 58px; flex: none; }
  .phone-number {
    font-size: 62px;
    line-height: 1;
    color: var(--white);
  }
</style>
</head>
<body>
  <main class="billboard">
    <header class="brand">
      <div class="brand-mark" aria-hidden="true"></div>
      <h1 class="brand-name">
        <span class="primary">Harlow Brook</span>
        <span class="secondary">Dentistry</span>
      </h1>
    </header>

    <div class="web-band"></div>
    <p class="website">Harlowbrookdentistry.example</p>

    <div class="phone-pill">
      <svg class="phone-icon" viewBox="0 0 40 58" aria-hidden="true">
        <path d="M30 4 C18 6 8 18 8 32 C8 44 14 52 22 56 L28 47 C22 43 19 38 19 31 C19 23 24 17 30 15 Z" fill="var(--navy)"/>
        <rect x="27" y="1" width="9" height="15" rx="3" transform="rotate(20 31 8)" fill="var(--navy)"/>
        <rect x="20" y="44" width="9" height="14" rx="3" transform="rotate(35 24 51)" fill="var(--navy)"/>
      </svg>
      <span class="phone-number">(555) 847-1390</span>
    </div>
  </main>
</body>
</html>
```